Concierge Healthcare Business Card Design and Logo

We need a logo and business card design for a new company called "Sound Haven". We will provide concierge audiological care, hearing aids, hearing exams, custom hearing protection etc to patients in the comfort of their homes and offices. We would like a sleek and modern design preferably with an Ear related logo.

Target Market(s)

People with hearing loss, Hunters, Musicians
My usual clientele are older individuals so usually 50+ years old

Industry/Entity Type

Health Care

Contact Information for Business Card

Celia Brandt, AuD
Audiologist
512-648-2917
soundhaven@mailvoro.com
www.soundhaven-vorel.com

Logo Text

Sound Haven

Number of Pages Required

3 page

```html
<!DOCTYPE html>
<html lang="en">
<head>
<meta charset="utf-8">
<title>Sound Haven – Business Card</title>
<link rel="stylesheet" href="https://fonts.googleapis.com/css2?family=Open+Sans:wght@400;600;700&family=Questrial&display=swap">
<style>
  :root {
    --backdrop: #161616;
    --card-white: #ffffff;
    --brand-orange: #f3891e;
    --ink: #3d3d3d;
    --ink-soft: #555555;
  }
  * { margin: 0; padding: 0; box-sizing: border-box; }
  html, body {
    width: 1200px; height: 900px; overflow: hidden;
    background: var(--backdrop);
  }
  .stage { position: relative; width: 1200px; height: 900px; }
  .card {
    position: absolute; top: 306px; width: 439px; height: 271px;
    border-radius: 10px; overflow: hidden;
  }
  .card--front { left: 149px; background: var(--card-white); }
  .card--back { left: 609px; background: var(--brand-orange); }

  .front-wordmark {
    position: absolute; left: 34px; top: 118px; width: 180px;
    text-align: center;
    font-family: "Open Sans", sans-serif; font-weight: 700;
    font-size: 27px; line-height: 1.1; color: var(--brand-orange);
  }

  .contact {
    position: absolute; left: 238px; top: 68px;
    font-family: "Open Sans", sans-serif; color: var(--ink);
    font-size: 12px; line-height: 15px;
  }
  .contact__name {
    font-weight: 600; font-size: 14.5px; line-height: 18px;
    color: var(--brand-orange);
  }
  .contact__role { color: var(--ink-soft); }
  .contact__address { margin-top: 12px; }
  .contact__lines { margin-top: 13px; list-style: none; }
  .contact__lines li {
    display: flex; align-items: center; gap: 7px; height: 16px;
  }
  .contact__icon { width: 9px; height: 9px; flex: none; fill: var(--brand-orange); }

  .back-wordmark {
    position: absolute; left: 0; right: 0; top: 170px;
    text-align: center;
    font-family: "Questrial", sans-serif; font-size: 35px;
    color: var(--card-white); letter-spacing: 0.3px;
  }
</style>
</head>
<body>
<main class="stage">
  <section class="card card--front" aria-label="Business card front">
    <div class="front-wordmark">Sound<br>Haven</div>
    <div class="contact">
      <p class="contact__name">Celia Brandt, AuD</p>
      <p class="contact__role">Audiologist</p>
      <p class="contact__address">12345, Address Goes Here<br>Country Name, 123456.</p>
      <ul class="contact__lines">
        <li>
          <svg class="contact__icon" viewBox="0 0 10 10" aria-hidden="true"><path d="M2 0.5 L3.6 2.6 L2.7 3.7 Q3.6 5.6 6.3 7.3 L7.4 6.4 L9.5 8 L8.3 9.6 Q3.8 9 0.4 1.7 Z"/></svg>
          <span>512-648-2917</span>
        </li>
        <li>
          <svg class="contact__icon" viewBox="0 0 10 10" aria-hidden="true"><path d="M0.5 2 H9.5 V8.2 H0.5 Z M1 2.3 L5 5.3 L9 2.3" stroke="#fff" stroke-width="0.8"/></svg>
          <span>soundhaven@mailvoro.com</span>
        </li>
        <li>
          <svg class="contact__icon" viewBox="0 0 10 10" aria-hidden="true"><circle cx="5" cy="5" r="4.6"/><path d="M0.6 5 H9.4 M5 0.4 Q2.5 5 5 9.6 M5 0.4 Q7.5 5 5 9.6" stroke="#fff" stroke-width="0.6" fill="none"/></svg>
          <span>www.soundhaven-vorel.com</span>
        </li>
      </ul>
    </div>
  </section>

  <section class="card card--back" aria-label="Business card back">
    <p class="back-wordmark">Sound Haven</p>
  </section>
</main>
</body>
</html>
```